Business Card Design For A Renovation Contractor Company

We need a business card for a new company based in Singapore, our company name is "RB Tolvane". We are a renovation contractor that builds designs into reality. We build more of F&B restaurants, retail stores and commercial offices. We work very closely with designers. The final design should communicate to our client that we are a company that you can trust, that will plan and complete your project without giving you a headache. I like my client to remember my company as "RB". The beauty of SIMPLE is important.

Industry/Entity Type

Contractor

Requirements
Nice to have
• Black or Red base

```html
<!DOCTYPE html>
<html lang="en">
<head>
<meta charset="utf-8">
<title>RB Tolvane — Business Cards</title>
<link rel="stylesheet" href="https://fonts.googleapis.com/css2?family=Arimo:wght@400;700&family=PT+Sans:wght@400&display=swap">
<style>
:root{
  --red:#ed1c24;
  --red-deep:#c9242a;
  --ink:#111111;
  --slate:#3a3a3c;
  --paper:#ffffff;
  --stage:#2b2320;
  --label:#f2f2f2;
  --muted:#333333;
}
*{margin:0;padding:0;box-sizing:border-box}
html,body{width:1200px;height:913px;overflow:hidden;background:var(--stage)}
.sheet{position:relative;width:1200px;height:913px;font-family:"Arimo",Arial,sans-serif}
.card{position:absolute;width:466px;height:265px;overflow:hidden;box-shadow:0 4px 10px rgba(0,0,0,.45)}
.side-label{position:absolute;font-family:"PT Sans",sans-serif;font-size:31px;color:var(--label)}

/* Front */
.card-front{left:91px;top:146px;background:var(--paper)}
.brand-dot{position:absolute;border-radius:50%}
.front-dot{left:101px;top:40px;width:66px;height:66px;border:6px solid var(--ink)}
.front-name{position:absolute;left:29px;top:112px;font-size:39px;font-weight:400;color:var(--ink);letter-spacing:-.5px;white-space:nowrap}
.front-tagline{position:absolute;left:32px;top:157px;font-size:14px;color:var(--ink);border-top:1px solid var(--ink);padding-top:1px;white-space:nowrap}
.contact{position:absolute;left:297px;top:76px;font-family:"PT Sans",sans-serif;font-size:12px;color:var(--muted);line-height:16px}
.contact li{list-style:none;display:flex;align-items:center;gap:5px}
.contact svg{width:9px;height:9px;fill:var(--red)}
.address{position:absolute;left:297px;top:134px;font-family:"PT Sans",sans-serif;font-size:12px;color:var(--muted);line-height:17px}
.name-bar{position:absolute;left:16px;top:215px;width:300px;height:26px;background:var(--ink);border-radius:13px;color:var(--paper);font-size:17px;line-height:26px;padding-left:50px;letter-spacing:.5px}
.role-bar{position:absolute;left:266px;top:215px;width:220px;height:26px;background:var(--red);border-radius:13px 0 0 13px;color:var(--paper);font-size:16px;line-height:26px;padding-left:31px}

/* Back 1 */
.card-back-dark{left:596px;top:146px;background:var(--slate)}
.dark-dot{left:168px;top:41px;width:122px;height:122px;border:6px solid var(--red)}
.dark-web-bar{position:absolute;left:186px;top:214px;width:262px;height:29px;background:var(--ink);border-radius:15px;color:var(--paper);font-size:13px;letter-spacing:3px;line-height:29px;padding-left:50px}
.dark-red-bar{position:absolute;left:0;top:214px;width:198px;height:29px;background:var(--red);border-radius:0 15px 15px 0}

/* Back 2 */
.card-back-red{left:91px;top:437px;background:var(--red)}
.red-dot{left:186px;top:50px;width:84px;height:84px;border:7px solid var(--paper)}
.red-name{position:absolute;left:0;right:0;top:138px;text-align:center;font-size:45px;font-weight:400;color:var(--paper);white-space:nowrap}
.red-tagline{position:absolute;left:0;right:0;top:187px;text-align:center;font-size:16px;font-weight:700;color:var(--paper)}

/* Back 3 */
.card-back-web{left:599px;top:438px;background:var(--red)}
.web-ring{left:209px;top:6px;width:252px;height:252px;border:20px solid var(--red-deep)}
.web-address{position:absolute;left:38px;top:227px;font-size:13px;letter-spacing:3px;color:var(--ink)}
</style>
</head>
<body>
<main class="sheet">
  <span class="side-label" style="left:944px;top:90px">Back 1</span>
  <span class="side-label" style="left:127px;top:736px">Back 2</span>
  <span class="side-label" style="left:980px;top:732px">Back 3</span>

  <section class="card card-front" aria-label="Card front">
    <span class="brand-dot front-dot"></span>
    <h1 class="front-name">RB Tolvane</h1>
    <p class="front-tagline">from plan to finished space</p>
    <ul class="contact">
      <li><svg viewBox="0 0 10 10"><path d="M2 0h2l1 3-1.5 1a6 6 0 0 0 2.5 2.5L7 5l3 1v2a2 2 0 0 1-2 2A8 8 0 0 1 0 2a2 2 0 0 1 2-2z"/></svg>012.555.0142</li>
      <li><svg viewBox="0 0 10 10"><path d="M0 2h10v6H0z M0 2l5 3.5L10 2" /></svg>info@rbtolvane.com</li>
      <li><svg viewBox="0 0 10 10"><circle cx="5" cy="5" r="5"/></svg>www.rbtolvane.com</li>
    </ul>
    <p class="address">Suite 000, RB building,<br>Cityname, country name</p>
    <div class="name-bar">YOURNAME HERE</div>
    <div class="role-bar">Director</div>
  </section>

  <section class="card card-back-dark" aria-label="Card back, dark">
    <span class="brand-dot dark-dot"></span>
    <div class="dark-web-bar">www.rbtolvane.com</div>
    <div class="dark-red-bar"></div>
  </section>

  <section class="card card-back-red" aria-label="Card back, red">
    <span class="brand-dot red-dot"></span>
    <h2 class="red-name">RB Tolvane</h2>
    <p class="red-tagline">from plan to finished space</p>
  </section>

  <section class="card card-back-web" aria-label="Card back, website">
    <span class="brand-dot web-ring"></span>
    <p class="web-address">www.rbtolvane.com</p>
  </section>
</main>
</body>
</html>
```